PixelHarbor Rangers (Ledgerline Nova)
A website dedicated to crypto education. We are a new company focused on blockchain edutainment (education and interesting and entertaining content about the blockchain space). We want a fun, clean/minimalist and modern website that is made up of an education platform which could be a website in it’s own right. It will be the reference point for our users/community for all of our other blockchain based content in the PHR website ecosystem which will be covering; crypto news, digital asset investing (including a technical and fundamental analysis subscription service), blockchain business solutions and an NFT section that will cover creative art projects (art, music, gaming and more). To feature a logins and payment system which may need a shopping basket set up for tutorial/educational platform that is accessed via the website, NFT page with sub-categories: education and NFT and metaverse/virtual world and merchandise shopping page which is Web 3.0 enabled (able to link to a VeloPurse, Kindle Vault etc , digital asset education page featuring blog and newsletter subscriptions links, A social media page where people can access videos, podcasts and our presence on other platforms such as Chirplo, Snapmora, Huddlex, Wirepost etc.
Number of Pages Required
5+ page
Look and feel

```html
<!DOCTYPE html>
<html lang="en">
<head>
<meta charset="utf-8">
<title>PixelHarbor Rangers</title>
<link rel="stylesheet" href="https://fonts.googleapis.com/css2?family=VT323&family=Lato:wght@400;700&display=swap">
<style>
:root{
  --bg:#0b0816;
  --bg-band:#1a0c28;
  --hero-shade:#1c1433;
  --card:#130e2c;
  --card-line:#3a2f7c;
  --btn-line:#5b46e0;
  --pink:#e23cf3;
  --cyan:#6ef6ff;
  --text:#ffffff;
  --muted:#cfc8e6;
  --pixel:"VT323", monospace;
  --sans:"Lato", sans-serif;
}
*{margin:0;padding:0;box-sizing:border-box}
html,body{width:1200px;height:4199px;overflow:hidden}
body{background:var(--bg);color:var(--text);font-family:var(--sans);position:relative}
.abs{position:absolute}
.hero-shade{left:260px;top:0;width:940px;height:620px;background:radial-gradient(ellipse at 70% 30%,#2a1d4a 0%,var(--hero-shade) 45%,transparent 75%);border-bottom-left-radius:420px}
.logo{left:109px;top:38px;font-family:var(--pixel);font-size:33px;letter-spacing:1px}
.nav{left:440px;top:43px;display:flex;gap:28px;font-size:17px}
.nav span:first-child{font-weight:700}
.cart{left:1046px;top:40px}
.cart-badge{left:1066px;top:28px;width:20px;height:20px;border-radius:50%;background:#5b3df0;font-size:12px;text-align:center;line-height:20px}
.ghost{border-radius:60px 60px 12px 12px;background:linear-gradient(#f4f4f8,#cfd0dc)}
.ghost-shadow{height:14px;border-radius:50%;background:rgba(120,110,160,.25)}
.hero-quote{left:564px;top:214px;font-family:var(--pixel);font-size:39px;line-height:48px;color:var(--pink);letter-spacing:2px}
.btn{display:flex;align-items:center;justify-content:center;border:2px solid var(--btn-line);border-radius:14px;background:#120a2a;font-size:16px}
.btn.pixel{font-family:var(--pixel);font-size:17px;border-color:#b9a8ff;letter-spacing:1px}
.btn.active{border:3px solid var(--pink);box-shadow:0 0 0 2px var(--cyan) inset;background:#2b1466}
.scroll{left:1072px;top:456px;writing-mode:vertical-rl;font-size:11px;letter-spacing:1px}
.section-title{left:0;width:1200px;text-align:center;font-family:var(--pixel);font-size:44px;letter-spacing:2px}
.section-title::before,.section-title::after{content:"_";margin:0 28px}
.band{left:0;width:1200px;background:linear-gradient(180deg,var(--bg-band),#1f0c2a);border-radius:18px}
.eco-card{top:810px;width:227px;height:343px;background:var(--card);border:2px solid var(--card-line);border-radius:16px;text-align:center}
.eco-card.active{border:3px solid var(--pink);box-shadow:0 0 14px var(--cyan)}
.eco-card svg{margin-top:40px}
.eco-card h3{font-family:var(--pixel);font-weight:400;font-size:24px;line-height:28px;margin-top:22px;height:56px}
.eco-card p{font-size:16.5px;line-height:30px;color:var(--muted);margin-top:16px;padding:0 16px}
.tab{top:1418px;width:145px;height:58px;border-radius:30px}
.nft-card{top:1537px;width:299px;height:380px;border:2px solid #8d7be0;border-radius:12px;overflow:hidden;background:#150c2a}
.nft-img{height:225px;border-bottom:2px solid #c9c3ff}
.nft-card h4{font-family:var(--pixel);font-weight:400;font-size:24px;margin:20px 0 0 14px}
.nft-card p{font-size:17px;line-height:30px;color:var(--muted);margin:2px 14px 0 14px}
.nft-card .arrow{margin:6px 0 0 18px}
.tut-card{top:2313px;width:460px;height:260px;border:2px solid #5a46c8;border-radius:10px;background:#1c0f3c}
.tut-thumb{position:absolute;left:18px;top:18px;width:188px;height:221px;border-radius:10px}
.tut-card h4{position:absolute;left:232px;top:34px;font-family:var(--pixel);font-weight:400;font-size:24px;letter-spacing:1px}
.tut-card p{position:absolute;left:232px;top:78px;width:210px;font-size:17px;line-height:30px;color:var(--muted)}
.socials{position:absolute;left:232px;top:207px;display:flex;gap:10px;font-size:12px;color:var(--text)}
.circle-btn{width:62px;height:62px;border-radius:50%;background:rgba(255,255,255,.85);display:flex;align-items:center;justify-content:center}
.video{left:111px;top:2848px;width:978px;height:452px;border-radius:12px;border:2px solid #3c2a7a;background:radial-gradient(circle at 62% 40%,#c0338d 0%,#5a1a8f 35%,#2a0f5c 70%,#170a3a 100%)}
.slide-arrow{top:3060px}
.edu-text{left:191px;top:3568px;width:820px;text-align:center;font-size:17.5px;line-height:30px;color:var(--muted)}
.btn.round{border-radius:30px;height:58px;width:145px;top:3734px;font-size:18px}
.brand-mark{left:223px;top:3810px;font-family:var(--pixel);font-size:64px;letter-spacing:4px;line-height:60px}
.footer-shade{left:0;top:3880px;width:1200px;height:319px;background:radial-gradient(ellipse at 80% 0%,#1b1430 0%,var(--bg) 60%)}
.footer-title{left:0;width:1200px;top:3938px;text-align:center;font-family:var(--pixel);font-size:33px;letter-spacing:1px}
.footer-social{left:0;width:1200px;top:4004px;display:flex;justify-content:center;gap:22px;font-size:15px}
.footer-nav{left:0;width:1200px;top:4047px;display:flex;justify-content:center;gap:28px;font-size:17px}
.pay{left:0;width:1200px;top:4093px;display:flex;justify-content:center;gap:8px}
.pay span{width:30px;height:20px;border-radius:3px;background:#e8e8ee}
.copy{left:0;width:1200px;top:4133px;text-align:center;font-size:15px;color:var(--muted)}
.wallet{left:26px;width:56px;height:56px;border-radius:12px;background:#fff;color:#1a1433;font-size:10px;font-weight:700;display:flex;align-items:center;justify-content:center;text-align:center;line-height:12px}
</style>
</head>
<body>

<header>
  <div class="abs hero-shade"></div>
  <div class="abs logo">PIXELHARBOR RANGERS</div>
  <nav class="abs nav"><span>Home</span><span>PHR Ecosystem</span><span>NFT Art</span><span>Education &amp; NFT</span><span>Blog</span><span>Contact</span></nav>
  <svg class="abs cart" width="26" height="26" viewBox="0 0 24 24" fill="none" stroke="#fff" stroke-width="1.8"><path d="M2 3h3l2.5 12h11l2-8H6.5"/><circle cx="9" cy="20" r="1.5"/><circle cx="17" cy="20" r="1.5"/></svg>
  <div class="abs cart-badge">1</div>
</header>

<section class="hero">
  <div class="abs ghost" style="left:114px;top:130px;width:188px;height:212px" role="img" aria-label="Pixel ghost mascot illustration"></div>
  <div class="abs ghost-shadow" style="left:120px;top:368px;width:176px"></div>
  <div class="abs ghost" style="left:334px;top:323px;width:188px;height:212px" role="img" aria-label="Second pixel ghost mascot illustration"></div>
  <div class="abs ghost-shadow" style="left:340px;top:562px;width:176px"></div>
  <div class="abs hero-quote">JUST BECAUSE YOU CAN'T HOLD IT,<br>DOESN'T MEAN YOU CAN'T OWN IT</div>
  <svg class="abs" style="left:944px;top:324px" width="30" height="30" viewBox="0 0 30 30" fill="none" stroke="#fff" stroke-width="1.6"><path d="M24 3c2 10-4 18-16 20"/><path d="M12 17l-5 6 7 2"/></svg>
  <div class="abs btn pixel" style="left:564px;top:349px;width:165px;height:63px">USER COMMUNITY</div>
  <div class="abs btn pixel" style="left:752px;top:349px;width:166px;height:63px">REGISTER</div>
  <div class="abs scroll">SCROLL DOWN</div>
  <svg class="abs" style="left:1075px;top:545px" width="22" height="36" viewBox="0 0 22 36" fill="none" stroke="#fff" stroke-width="2"><path d="M11 2v30M3 24l8 9 8-9"/></svg>
</section>

<section class="ecosystem">
  <h2 class="abs section-title" style="top:690px">PHR ECOSYSTEM</h2>
  <div class="abs eco-card" style="left:109px">
    <svg width="70" height="62" viewBox="0 0 70 62" fill="none" stroke="#fff" stroke-width="2.5"><rect x="8" y="4" width="58" height="54" rx="3"/><path d="M8 16H3v36a6 6 0 0 0 6 6"/><rect x="16" y="14" width="18" height="16"/><path d="M40 16h18M40 24h18M16 38h42M16 46h42"/></svg>
    <h3>CRYPTO NEWS</h3>
    <p>Duis aute irure dolor reprehenderit in volupt velit esse cillum.</p>
  </div>
  <div class="abs eco-card" style="left:360px">
    <svg width="70" height="62" viewBox="0 0 70 62" fill="none" stroke="#fff" stroke-width="2.5"><rect x="22" y="2" width="26" height="58" rx="5"/><circle cx="35" cy="30" r="10"/><path d="M35 24v12M32 27h5M33 33h5M4 22h14M4 30h14M52 22h14M52 38h14"/></svg>
    <h3>DIGITAL ASSET<br>INVESTING</h3>
    <p>Duis aute irure dolor reprehenderit in volupt velit esse cillum.</p>
  </div>
  <div class="abs eco-card active" style="left:611px">
    <svg width="70" height="70" viewBox="0 0 70 70" fill="none" stroke="#fff" stroke-width="2.5" style="margin-top:36px"><path d="M35 3l29 16v32L35 67 6 51V19z"/><path d="M35 10l23 13v24L35 60 12 47V23z"/><path d="M22 38h26M26 45h18"/><text x="35" y="31" text-anchor="middle" font-family="VT323, monospace" font-size="15" fill="#fff" stroke="none">NFT</text></svg>
    <h3 style="margin-top:18px">NFT</h3>
    <p>Duis aute irure dolor reprehenderit in volupt velit esse cillum.</p>
  </div>
  <div class="abs eco-card" style="left:862px">
    <svg width="66" height="66" viewBox="0 0 66 66" fill="none" stroke="#fff" stroke-width="2.5"><path d="M33 4l26 15v28L33 62 7 47V19z"/><path d="M33 18l14 8v16l-14 8-14-8V26z"/><path d="M19 26l14 8 14-8M33 34v16"/></svg>
    <h3>BLOCKCHAIN<br>BUSINESS SOL</h3>
    <p>Duis aute irure dolor reprehenderit in volupt velit esse cillum.</p>
  </div>
</section>

<section class="nft-art">
  <div class="abs band" style="top:1250px;height:772px"></div>
  <h2 class="abs section-title" style="top:1321px">NFT ART</h2>
  <div class="abs btn tab" style="left:326px">Music</div>
  <div class="abs btn tab active" style="left:527px">Gaming</div>
  <div class="abs btn tab" style="left:729px">Art</div>
  <article class="abs nft-card" style="left:112px">
    <div class="nft-img" style="background:linear-gradient(180deg,#e24d9a 0%,#a23ab8 45%,#3d2b6e 75%,#2a2450 100%)" role="img" aria-label="Pixel art city skyline at dusk"></div>
    <h4>NFT Game</h4>
    <p>Duis aute irure dolor in re it in voluptate velit esse cillum dolore.</p>
    <svg class="arrow" width="20" height="12" viewBox="0 0 20 12" fill="none" stroke="#fff" stroke-width="1.5"><path d="M1 6h17M13 1l5 5-5 5"/></svg>
  </article>
  <article class="abs nft-card" style="left:452px">
    <div class="nft-img" style="background:linear-gradient(180deg,#4a54d8 0%,#5fb3ee 45%,#6fd3e0 70%,#e2a055 100%)" role="img" aria-label="Pixel art beach with palm trees"></div>
    <h4>NFT Game</h4>
    <p>Duis aute irure dolor in re it in voluptate velit esse cillum dolore.</p>
    <svg class="arrow" width="20" height="12" viewBox="0 0 20 12" fill="none" stroke="#fff" stroke-width="1.5"><path d="M1 6h17M13 1l5 5-5 5"/></svg>
  </article>
  <article class="abs nft-card" style="left:791px">
    <div class="nft-img" style="background:linear-gradient(180deg,#3a1c96 0%,#6a2cd8 45%,#9a3df0 70%,#4d1f9c 100%)" role="img" aria-label="Pixel art purple mountains under moonlit sky"></div>
    <h4>NFT Game</h4>
    <p>Duis aute irure dolor in re it in voluptate velit esse cillum dolore.</p>
    <svg class="arrow" width="20" height="12" viewBox="0 0 20 12" fill="none" stroke="#fff" stroke-width="1.5"><path d="M1 6h17M13 1l5 5-5 5"/></svg>
  </article>
</section>

<section class="tutorial">
  <h2 class="abs section-title" style="top:2100px">BLOCKCHAIN TUTORIAL</h2>
  <div class="abs btn round" style="left:439px;top:2198px">Free</div>
  <div class="abs btn round active" style="left:615px;top:2198px">Paid</div>
  <article class="abs tut-card" style="left:111px">
    <div class="tut-thumb" style="background:linear-gradient(135deg,#0f2a2e,#1d3a3a 40%,#6a5a22 60%,#0c1a22)" role="img" aria-label="Abstract golden cube render"></div>
    <div class="abs circle-btn" style="left:81px;top:97px"><svg width="22" height="24" viewBox="0 0 22 24"><path d="M3 2l17 10L3 22z" fill="#111"/></svg></div>
    <h4>VIDEO TUTORIALS</h4>
    <p>Sed ut perspiciatis unde omnis iste natus errorit voluptate accusant.</p>
    <div class="socials"><span>Snapmora</span><span>Chirplo</span><span>Huddlex</span><span>Wirepost</span></div>
  </article>
  <article class="abs tut-card" style="left:628px">
    <div class="tut-thumb" style="background:radial-gradient(circle,#2e5fb0 0%,#173270 45%,#0c1836 100%)" role="img" aria-label="Circuit board chip artwork"></div>
    <div class="abs circle-btn" style="left:81px;top:97px"><svg width="26" height="24" viewBox="0 0 26 24" fill="none" stroke="#111" stroke-width="2.5"><path d="M3 18v-5a10 10 0 0 1 20 0v5"/><rect x="2" y="14" width="5" height="8" rx="1" fill="#111"/><rect x="19" y="14" width="5" height="8" rx="1" fill="#111"/></svg></div>
    <h4>AUDIO TUTORIALS</h4>
    <p>Sed ut perspiciatis unde omnis iste natus errorit voluptate accusant.</p>
    <div class="socials"><span>Snapmora</span><span>Chirplo</span><span>Huddlex</span><span>Wirepost</span></div>
  </article>
</section>

<section class="nft-education">
  <div class="abs band" style="top:2671px;height:725px"></div>
  <h2 class="abs section-title" style="top:2739px">NFT EDUCATION</h2>
  <div class="abs video" role="img" aria-label="Neon virtual reality scene with wireframe landscape"></div>
  <div class="abs circle-btn" style="left:575px;top:3050px;width:48px;height:48px;background:#fff"><svg width="18" height="20" viewBox="0 0 18 20"><path d="M3 2l13 8-13 8z" fill="#111"/></svg></div>
  <svg class="abs slide-arrow" style="left:36px" width="26" height="30" viewBox="0 0 26 30" fill="none" stroke="#6b5aa8" stroke-width="2"><path d="M24 15H3M10 8l-7 7 7 7"/></svg>
  <svg class="abs slide-arrow" style="left:1133px" width="26" height="30" viewBox="0 0 26 30" fill="none" stroke="#fff" stroke-width="2"><path d="M2 15h21M16 8l7 7-7 7"/></svg>
</section>

<section class="asset-education">
  <h2 class="abs section-title" style="top:3473px">DIGITAL ASSERT EDUCATION</h2>
  <p class="abs edu-text">Nam libero tempore, cum soluta nobis est eligendi optio cum nihil impedit quo minus id quod maxime placeat facere possimus, omnis voluptas assumenda est, omnis dolor repellendus. Temporibus autem quibusdam et aut officiis debitis aut rerum necessitatibus saepe eveniet ut et voluptates repudianda et molestiae non recusandae.</p>
  <svg class="abs" style="left:360px;top:3738px" width="48" height="34" viewBox="0 0 48 34" fill="none" stroke="#fff" stroke-width="2"><path d="M3 31C8 16 22 8 42 10"/><path d="M35 3l8 7-8 6"/></svg>
  <div class="abs btn round" style="left:439px">Sign Up</div>
  <div class="abs btn round active" style="left:615px">Blog</div>
</section>

<footer>
  <div class="abs footer-shade"></div>
  <div class="abs brand-mark">PHR</div>
  <div class="abs footer-title">PIXELHARBOR RANGERS</div>
  <div class="abs footer-social"><span>Snapmora</span><span>Chirplo</span><span>Huddlex</span><span>Wirepost</span></div>
  <nav class="abs footer-nav"><span>Home</span><span>PHR Ecosystem</span><span>NFT art</span><span>Education &amp; NFT</span><span>Blog</span><span>Contact</span></nav>
  <div class="abs pay"><span></span><span></span><span></span><span></span><span></span><span></span></div>
  <p class="abs copy">2022 PixelHarbor Rangers.All Rights Reserved.</p>
  <div class="abs wallet" style="top:3953px">Kindle<br>Vault</div>
  <div class="abs wallet" style="top:4022px">Velo<br>Purse</div>
</footer>

</body>
</html>
```